B2B flyer solution for charging infrastructures (One-Pager Din A4, double-sided)

We need a professional design for our flyer in format Din A4/both sides.
Attached you will find the content for the flyer, but we are looking for a modern, professional design.

Some background/context information:
- the product is about a solution for charging and billing of charging infrastructures (for electric cars) in companies
- target group: companies, esp. facility managers, fleet managers, controlling, CTO, CEO
- should be printed and available online
- our website (and most of our current design work): https://wendavo-netz.de

In the files you will find:
- photos of reference implementations of our solution (should be included in the flyer)
- stock photos (we are using the one you will find in the current flyer on our presentations, maybe you can use it too to keep some corporate identity.
- our logo
- the current flyer as PDF and as PowerPoint
- a sample presentation we also need for customer communication

It would be nice if the design will align with the existing design work, but bring fresh aspects and will be up-to-date and professional.

Target Market(s)

B2B, companies, fleet managers, facility managers, CTO, CIO

Industry/Entity Type

Enterprises, Charging Solutions for Electric Vehicles

Requirements
Nice to have
• Bright, light design, clean, readable

```html
<!DOCTYPE html>
<html lang="de">
<head>
<meta charset="utf-8">
<title>Wendavo-Netz Professional – Flyer Vorder- und Rückseite</title>
<link href="https://fonts.googleapis.com/css2?family=Poppins:wght@400;500;600;700;800&display=swap" rel="stylesheet">
<style>
  :root{
    --magenta:#e0179a;
    --purple:#8a2cc9;
    --violet:#6a2bb8;
    --ink:#1b1b1f;
    --band:#232325;
    --grey-box:#cfcfd1;
    --paper:#ffffff;
    --backdrop:#f1f1f3;
    --text:#222;
  }
  *{box-sizing:border-box;margin:0;padding:0}
  html,body{width:816px;height:1200px;overflow:hidden;background:var(--backdrop)}
  body{font-family:"Poppins",sans-serif;color:var(--text);position:relative}

  .page{position:absolute;top:327px;width:583px;height:825px;background:var(--paper);overflow:hidden;
    transform:scale(.66);transform-origin:0 0;box-shadow:0 6px 24px rgba(0,0,0,.12)}
  .page--front{left:15px}
  .page--back{left:416px}
  .page > *{position:absolute}

  .hero{left:0;top:0}
  .brand{left:30px;top:30px;display:flex;align-items:center;gap:8px;font-weight:500;font-size:21px;color:var(--ink);letter-spacing:-.3px;z-index:2}
  .brand-dot{width:14px;height:14px;border-radius:50%;background:var(--magenta)}

  .title{left:28px;top:82px;line-height:1;z-index:2}
  .title-main{display:block;font-weight:800;font-size:28px;letter-spacing:.3px;
    background:linear-gradient(90deg,var(--magenta),var(--purple));-webkit-background-clip:text;background-clip:text;color:transparent}
  .title-sub{display:block;font-weight:700;font-size:28px;color:var(--ink);margin-top:4px}
  .title-rule{left:28px;top:156px;width:190px;height:2px;background:linear-gradient(90deg,var(--magenta),var(--purple))}
  .subtitle{left:30px;top:166px;font-size:12.5px;line-height:1.2;color:var(--ink);width:175px}
  .subtitle--wide{width:260px;top:170px;font-size:14px}

  .intro-band{left:0;top:223px;width:583px;height:80px;background:var(--band)}
  .intro-text{left:30px;top:232px;width:180px;font-size:9px;line-height:1.2;color:#fff}
  .intro-claim{left:30px;top:284px;font-size:8px;color:var(--magenta)}

  .tick-list{list-style:none}
  .tick-list li{position:relative;padding-left:15px;font-weight:600;font-size:9px;line-height:1.25;color:var(--ink);margin-bottom:11px}
  .tick-list li::before{content:"";position:absolute;left:0;top:2px;width:7px;height:7px;border:1.3px solid var(--magenta);border-radius:50%}
  .tick-list li::after{content:"";position:absolute;left:2.3px;top:4px;width:3px;height:1.5px;border-left:1.2px solid var(--magenta);border-bottom:1.2px solid var(--magenta);transform:rotate(-45deg)}
  .tick-list--light li{font-weight:400;font-size:8.5px;margin-bottom:9px}

  .services{left:30px;top:330px;width:265px;height:180px;background:var(--grey-box);border-radius:10px}
  .services-tab{position:absolute;left:58px;top:-5px;width:150px;height:38px;background:linear-gradient(90deg,var(--purple),var(--magenta));
    clip-path:polygon(0 0,100% 0,88% 100%,12% 100%);color:#fff;font-weight:600;font-size:17px;text-align:center;line-height:37px}
  .services .tick-list{position:absolute;left:12px;top:50px;width:245px}
  .services .tick-list li{margin-bottom:12px}

  .tablet{left:360px;top:320px;width:163px;height:215px;border-radius:12px;background:linear-gradient(160deg,#2a2a2e,#0d0d10);padding:7px}
  .tablet-screen{width:100%;height:100%;border-radius:4px;background:linear-gradient(180deg,#fafafa,#e8e6ee)}

  .car-visual{left:0;top:538px;width:295px;height:135px;
    background:radial-gradient(ellipse at 55% 55%,#e9eef2 0%,#b9c6d0 45%,rgba(255,255,255,0) 72%)}

  .section-head{font-weight:600;font-size:13.5px;line-height:1.2;color:var(--purple)}
  .benefits{left:313px;top:558px;width:250px}
  .benefits .tick-list{margin-top:12px}

  .contact{left:30px;top:695px;width:250px}
  .contact p{margin-top:10px;font-size:8.5px;line-height:1.25;color:var(--ink)}

  .call{font-weight:700;font-size:14px;color:var(--magenta)}
  .contact-line{display:flex;align-items:center;gap:16px;font-weight:600;font-size:8.5px;color:var(--ink)}
  .contact-line span{display:flex;align-items:center;gap:6px}
  .tagline{font-weight:600;font-size:8.5px;line-height:1.3;color:var(--violet)}
  .page--front .call{left:313px;top:728px}
  .page--front .contact-line{left:315px;top:756px}
  .page--front .tagline{left:313px;top:780px}
  .page--back .call{left:313px;top:737px}
  .page--back .contact-line{left:315px;top:763px}
  .page--back .tagline{left:313px;top:785px}

  .footer-band{left:0;top:773px;width:320px;height:52px;background:linear-gradient(90deg,var(--magenta),var(--purple));clip-path:polygon(0 0,95% 0,100% 100%,0 100%)}
  .footer-url{left:32px;top:784px;font-weight:700;font-size:20px;letter-spacing:1px;color:#fff}
  .footer-rule{left:310px;top:818px;width:273px;height:7px;background:linear-gradient(90deg,var(--purple),var(--violet))}

  /* back page */
  .usage-band{left:0;top:205px;width:583px;height:133px;background:var(--band)}
  .usage-title{left:0;top:212px;width:583px;text-align:center;font-weight:600;font-size:13px;color:#fff}
  .usage-groups{left:20px;top:245px;width:543px;display:flex;justify-content:space-between}
  .usage-item{flex:1;display:flex;flex-direction:column;align-items:center;gap:6px;text-align:center;font-weight:600;font-size:7.5px;line-height:1.2;color:#fff;border-right:1px dashed #777}
  .usage-item:last-child{border-right:none}
  .usage-icon{width:44px;height:44px;border-radius:50%;background:linear-gradient(135deg,var(--purple),var(--magenta));display:flex;align-items:center;justify-content:center}

  .col{width:260px}
  .col p{font-size:8px;line-height:1.2;color:var(--ink);margin:4px 0 8px}
  .col-left{left:28px;top:348px}
  .col-left-2{left:28px;top:557px}
  .col-right{left:300px;top:348px;width:265px}
  .photo-grid{left:305px;top:543px;width:248px;height:182px;display:grid;grid-template-columns:1fr 1fr;gap:6px}
  .photo-grid div{border-radius:4px}
</style>
</head>
<body>

<!-- Vorderseite -->
<main class="page page--front">
  <div class="intro-band"></div>
  <svg class="hero" width="583" height="303" viewBox="0 0 583 303">
    <defs>
      <linearGradient id="arcGradA" x1="0" y1="0" x2="1" y2="1"><stop offset="0" stop-color="#8a2cc9"/><stop offset="1" stop-color="#e0179a"/></linearGradient>
      <linearGradient id="garage" x1="0" y1="0" x2="0" y2="1"><stop offset="0" stop-color="#8d8c88"/><stop offset=".55" stop-color="#4c4b49"/><stop offset="1" stop-color="#1e1e20"/></linearGradient>
    </defs>
    <circle cx="560" cy="60" r="270" fill="url(#garage)" role="img" aria-label="Photo: dark electric SUV in a concrete garage next to a wall charging station"/>
    <circle cx="560" cy="60" r="272" fill="none" stroke="url(#arcGradA)" stroke-width="7"/>
  </svg>

  <div class="brand"><span class="brand-dot"></span>wendavo-netz.de</div>
  <h1 class="title"><span class="title-main">WENDAVO-NETZ</span><span class="title-sub">PROFESSIONAL</span></h1>
  <div class="title-rule"></div>
  <p class="subtitle">die maßgeschneiderte B2B-Abrechnungslösung für Elektromobilität</p>

  <p class="intro-text">Lade-Infrastruktur-Abrechnungslösungen für Unternehmen, damit Lade-Infrastruktur Erträge statt Kosten produziert.</p>
  <p class="intro-claim">So wird Lade-Infrastruktur von einer Kostenstelle zu einem Profitcenter.</p>

  <section class="services">
    <div class="services-tab">LEISTUNGEN</div>
    <ul class="tick-list">
      <li>Vielseitige Abrechnungsmöglichkeiten für Fuhrpark, Mitarbeiter, Partnerunternehmen, Mieter, Kunden und andere.</li>
      <li>Full-Service-Betreuung (Monitoring, Abrechnung, Benutzerbetreuung)</li>
      <li>Integration in ihre Unternehmensabläufe</li>
      <li>Berücksichtigung von Eigentümer/Mieter-Konstellationen</li>
    </ul>
  </section>

  <div class="tablet"><div class="tablet-screen" role="img" aria-label="Tablet showing a sample monthly charging statement"></div></div>
  <div class="car-visual" role="img" aria-label="Illustration: white electric car connected to a charging column"></div>

  <section class="benefits">
    <h2 class="section-head">MIT WENDAVO-NETZ PROFESSIONAL PROFITIEREN:</h2>
    <ul class="tick-list">
      <li>Effizienter Verwaltung von<br>Lade-Infrastruktur</li>
      <li>Umfassende Full-Service-Betreuung</li>
      <li>Nahtloser Integration in Ihre<br>kaufmännischen Prozesse</li>
      <li>Vielseitigen Abrechnungsmöglichkeiten</li>
    </ul>
  </section>

  <section class="contact">
    <h2 class="section-head">KONTAKTIEREN SIE UNS</h2>
    <p>Erfahren Sie mehr über wendavo-netz und wie wir Ihre Abrechnungsanforderungen erfüllen können. Kontaktieren Sie uns für eine kostenlose Beratung:</p>
  </section>

  <div class="call">RUF UNS HEUTE AN !</div>
  <div class="contact-line">
    <span><svg width="10" height="10" viewBox="0 0 24 24"><path d="M6.6 10.8a15 15 0 0 0 6.6 6.6l2.2-2.2a1 1 0 0 1 1-.25 11.4 11.4 0 0 0 3.6.57 1 1 0 0 1 1 1V20a1 1 0 0 1-1 1A17 17 0 0 1 3 4a1 1 0 0 1 1-1h3.5a1 1 0 0 1 1 1c0 1.25.2 2.45.57 3.57a1 1 0 0 1-.25 1z" fill="#6a2bb8"/></svg>49 (0) 5550 246 810</span>
    <span><svg width="11" height="9" viewBox="0 0 24 18"><rect x="1" y="1" width="22" height="16" rx="2" fill="#6a2bb8"/><path d="M2 2l10 8 10-8" fill="none" stroke="#fff" stroke-width="2"/></svg>info@wendavo-netz.de</span>
  </div>
  <p class="tagline">WENDAVO-NETZ – DIE ABRECHNUNGSLÖSUNG<br>FÜR LADE-INFRASTRUKTUR IN UNTERNEHMEN.</p>

  <div class="footer-band"></div>
  <div class="footer-url">www.wendavo-netz.de</div>
  <div class="footer-rule"></div>
</main>

<!-- Rückseite -->
<main class="page page--back">
  <div class="usage-band"></div>
  <svg class="hero" width="583" height="210" viewBox="0 0 583 210">
    <defs>
      <linearGradient id="arcGradB" x1="0" y1="0" x2="1" y2="1"><stop offset="0" stop-color="#8a2cc9"/><stop offset="1" stop-color="#e0179a"/></linearGradient>
      <radialGradient id="charge" cx=".7" cy=".6" r=".7"><stop offset="0" stop-color="#3d6fe0"/><stop offset=".5" stop-color="#c9d6ea"/><stop offset="1" stop-color="#eef2f8"/></radialGradient>
    </defs>
    <circle cx="500" cy="15" r="188" fill="url(#charge)" role="img" aria-label="Photo: charging plug inserted into a white electric car with blue glowing port"/>
    <circle cx="500" cy="15" r="190" fill="none" stroke="url(#arcGradB)" stroke-width="6"/>
  </svg>

  <div class="brand"><span class="brand-dot"></span>wendavo-netz.de</div>
  <h1 class="title"><span class="title-main">WENDAVO-NETZ</span><span class="title-sub">PROFESSIONAL</span></h1>
  <div class="title-rule"></div>
  <p class="subtitle subtitle--wide">die Funktionen im Überblick</p>

  <div class="usage-title">Verrechnung von Ladevorgängen für</div>
  <div class="usage-groups">
    <div class="usage-item"><span class="usage-icon"><svg width="24" height="16" viewBox="0 0 24 16"><path d="M3 9l2-5h14l2 5v4H3z" fill="#fff"/><circle cx="7" cy="13" r="2" fill="#c0208f"/><circle cx="17" cy="13" r="2" fill="#c0208f"/></svg></span>Fuhrpark,<br>Dienstwagen</div>
    <div class="usage-item"><span class="usage-icon"><svg width="20" height="22" viewBox="0 0 20 22"><circle cx="10" cy="6" r="4.5" fill="#fff"/><path d="M2 21c0-5 3.5-8 8-8s8 3 8 8z" fill="#fff"/></svg></span>Mitarbeiter<br>Privatfahrzeuge</div>
    <div class="usage-item"><span class="usage-icon"><svg width="20" height="22" viewBox="0 0 20 22"><circle cx="12" cy="4" r="3" fill="#fff"/><path d="M8 9h7v6h-2v6h-3v-6H8z" fill="#fff"/><rect x="3" y="10" width="2" height="11" fill="#fff"/></svg></span>Kunden<br>und Gäste</div>
    <div class="usage-item"><span class="usage-icon"><svg width="24" height="20" viewBox="0 0 24 20"><path d="M12 2l10 8h-3v9H5v-9H2z" fill="#fff"/><rect x="10" y="12" width="4" height="7" fill="#c0208f"/></svg></span>Vermieter,<br>Eigentümer</div>
  </div>

  <section class="col col-left">
    <h2 class="section-head">FULL-SERVICE-BETREUUNG FÜR SORGENFREIES MANAGEMENT</h2>
    <p>wendavo-netz übernimmt auf Wunsch alle organisatorischen Belange bei der Verwaltung Ihrer Lade-Infrastruktur, einschließlich:</p>
    <ul class="tick-list tick-list--light">
      <li>Monitoring</li>
      <li>Support</li>
      <li>User-Onboarding und -Support</li>
      <li>Handling von Zugangskarten</li>
      <li>Integration von firmeninternen Zugangstoken</li>
    </ul>
  </section>

  <section class="col col-left-2">
    <h2 class="section-head">PERFEKTE INTEGRATION IN KAUFMÄNNISCHE PROZESSE</h2>
    <p>wendavo-netz fügt sich nahtlos in die kaufmännischen Strukturen moderner Unternehmen ein und bietet:</p>
    <ul class="tick-list tick-list--light">
      <li>Erweitertes Reporting</li>
      <li>Aufschlüsselung und Tarifierung nach Nutzergruppe</li>
      <li>Unterstützung unternehmensinterner Abrechnung und Verrechnung und/oder Zahlungseinzug durch wendavo-netz</li>
      <li>Schnittstellen zu Buchhaltung und Lohnbuchhaltung</li>
      <li>Bedarfsgerechte Anpassbarkeit</li>
    </ul>
  </section>

  <section class="col col-right">
    <h2 class="section-head">BESONDERER ASPEKT: EIGENTÜMER-MIETER KONSTELLATIONEN</h2>
    <p>Häufige Situation: Der Mieter eines Objektes benötigt Lade-Infrastruktur, der Eigentümer/Verwalter möchte nicht zusätzlich belastet werden</p>
    <ul class="tick-list tick-list--light">
      <li>Unterschiedliche Betreibermodelle für verschiedene Situationen (Langzeit-Mieter vs. Kurzzeit-Mieter)</li>
      <li>Kauf-, Miet- und Leasing-Optionen</li>
      <li>Kostenneutral für Eigentümer/Verwalter durch geeignete Abrechnungsmodelle</li>
    </ul>
  </section>

  <div class="photo-grid">
    <div style="background:linear-gradient(160deg,#c7b98e,#4c4a45)" role="img" aria-label="Photo: row of charging columns in a parking lot"></div>
    <div style="background:linear-gradient(160deg,#1d2a4a,#8aa0c8)" role="img" aria-label="Photo: charging cable under a solar carport"></div>
    <div style="background:linear-gradient(160deg,#dfe6ef,#b9473f)" role="img" aria-label="Photo: charging plug at a white car"></div>
    <div style="background:linear-gradient(160deg,#1b2240,#5a6fb0)" role="img" aria-label="Photo: charging station at night with blue lights"></div>
  </div>

  <div class="call">RUF UNS HEUTE AN !</div>
  <div class="contact-line">
    <span><svg width="10" height="10" viewBox="0 0 24 24"><path d="M6.6 10.8a15 15 0 0 0 6.6 6.6l2.2-2.2a1 1 0 0 1 1-.25 11.4 11.4 0 0 0 3.6.57 1 1 0 0 1 1 1V20a1 1 0 0 1-1 1A17 17 0 0 1 3 4a1 1 0 0 1 1-1h3.5a1 1 0 0 1 1 1c0 1.25.2 2.45.57 3.57a1 1 0 0 1-.25 1z" fill="#6a2bb8"/></svg>49 (0) 5550 246 810</span>
    <span><svg width="11" height="9" viewBox="0 0 24 18"><rect x="1" y="1" width="22" height="16" rx="2" fill="#6a2bb8"/><path d="M2 2l10 8 10-8" fill="none" stroke="#fff" stroke-width="2"/></svg>info@wendavo-netz.de</span>
  </div>
  <p class="tagline">WENDAVO-NETZ – DIE ABRECHNUNGSLÖSUNG<br>FÜR LADE-INFRASTRUKTUR IN UNTERNEHMEN.</p>

  <div class="footer-band"></div>
  <div class="footer-url">www.wendavo-netz.de</div>
  <div class="footer-rule"></div>
</main>

</body>
</html>
```